Trade show flyer for award-winning, innovative folding helmet for cyclists

I am launching a brand new folding helmet for cyclists, skate boarders etc. It is being launched at a huge cycle show in Taiwan later this month and will be presented to special clients (corporates) who have been invited to view this stunning new product.
I have some pictures, a logo, a strap line and a little bit of copy that I would like to be included in the flyer.
I would like the flyer to be A4, colour both sides and probably folded once (to give 4 pages of A5)
The whole purpose of the flyer is to keep the helmet at the forefront of buyers minds when they return to their offices. This is a worlds first and an incredibly innovative, patented, trademarked product.
I need a glossy flyer that will appeal to cyclists and helmet manufacturers. The idea is to get big helmet brands to use our folding technology... almost (but not exactly) like an "brisco within" idea.
I have uploaded my logo and CG pictures of the product.
Updates

I will work on the copy and provide it ASAP. Certainly to any shortlisted designers. In the meantime, any text will do.

Also, I may decide to leave out the 2nd "we'll get you there" strap line.

                                       

I will add the text for the brochure  soon. Hopefully within 24 hours but quite possibly sooner.

Also, please forget about skate boarding etc as this is just for a bike show. So, for this project, just concentrate on the helmet being for cyclists.

The short time limit is because the show starts on March 20th and I have to have the flyers proofed, printed and delivered to Taipei by then!

Here is the text for the flyer: It's 159 words:

 

Vantrel is an incredibly innovative new helmet which folds flat for easy portability! (Current helmets are awkward to carry and research shows this is why 91% of urban bike scheme users don't use one.)

Vantrel looks stunning & is made to a superb standard by Quillon Gear, the world's largest helmet manufacturer.
It's made in specialist EPS, Nylon & PC layers.

Patented worldwide, Vantrel surpasses all relevant safety standards and its components are recyclable.
Vantrel folds & unfolds quickly and simply so it's perfect for cyclists who want to carry a helmet more easily.

It's comfortable, convenient & safe!

Vantrel is aimed at all urban cyclists. Eventually it will be marketed to all cyclists as well as other users of sports safety helmets (skiers, skaters, snow boarders, hockey players, horse riders etc)

Vantrel has won major innovation awards in the UK and Europe.

Vantrel’s flat profile will allow innovative selling methods such as at vending machines placed by major bicycle hire points.

Here is the Logo from Quillon Gear, which should also appear on the flyer, as they are the manufacturers

The contact email address is info@vantrelhelmet.example and the website is www.vantrelhelmet.example

Thanks

Please note that there are a couple of minor changes to the copy as well as some other changes that I wish to make.

If you've already submitted a design then please DON'T resubmit it with the changes. That would be unnecessary work and we can address these small changes later if you win.

Please ensure that a small, raised "TM" is used every time Vantrel is mentioned...

Also, please don't use the "Vantrel... we'll get you there" strap line as I've gone off it.

Here is the new amended text:

 

Vantrel looks stunning & is made to a superb standard by Quillon Gear, the world's largest OEM helmet manufacturer.

Vantrel is aimed at all cyclists. Eventually it will be marketed to other users of sports safety helmets such as skiers, skaters, snow boarders, hockey players, horse riders etc.

Target Market(s)

Senior management, Directors and owners of helmet brand companies

Industry/Entity Type

Trade

Requirements
Must have
• The logo, the pictures and the following text... Although some of this may be open to discussion...

Vantrel... an open and shut case for the future of helmets.

Vantrel... We'll get you there.

Winner Platinum Invention of the Year at the Global Ingenuity Prizes
Winner "Transport Safety" award at Kestra
Winner "Lumora Zenith gold award" for Innovation

And copy, around 100 words, to be discussed.
Nice to have
• Design should somehow reflect innovation and safety, if possible....

```html
<!DOCTYPE html>
<html lang="en">
<head>
<meta charset="utf-8">
<title>Vantrel — A Corporate With Recognition</title>
<link href="https://fonts.googleapis.com/css2?family=Arimo:ital,wght@0,400;0,700;1,700&display=swap" rel="stylesheet">
<style>
  :root {
    --ink: #111111;
    --body-ink: #2a3a22;
    --green: #7dc35b;
    --green-deep: #4f8a34;
    --green-pale: #e7f3e0;
    --green-panel: #d2e6c1;
    --blue: #4a9fd8;
    --charcoal: #555555;
    --line-grey: #6b6b6b;
    --paper: #ffffff;
  }
  * { margin: 0; padding: 0; box-sizing: border-box; }
  html, body { width: 1200px; height: 848px; overflow: hidden; background: var(--paper); }
  .sheet {
    position: relative; width: 1200px; height: 848px; overflow: hidden;
    background: var(--paper); font-family: "Arimo", Arial, sans-serif; color: var(--ink);
  }
  sup.tm { font-size: .55em; vertical-align: super; line-height: 0; font-weight: 700; }

  .rail-vertical { position: absolute; left: 1146px; top: 0; width: 16px; height: 848px; background: var(--green-pale); }
  .band-divider { position: absolute; left: 0; top: 485px; width: 1192px; height: 22px; background: var(--green-pale); }
  .band-faint { position: absolute; left: 0; top: 412px; width: 1196px; height: 16px; background: var(--green-pale); opacity: .55; }

  .headline {
    position: absolute; left: 49px; top: 76px;
    font-family: "Arimo", Arial, sans-serif; font-weight: 700;
    font-size: 53px; line-height: 54px; letter-spacing: -.3px; text-transform: uppercase;
    -webkit-text-stroke: 1.2px currentColor;
  }
  .headline .accent { color: var(--green); }

  .photo { position: absolute; border-radius: 14px; }
  .photo-award-helmet {
    left: 47px; top: 232px; width: 284px; height: 206px;
    background: radial-gradient(ellipse 70% 55% at 50% 55%, #2b2b2b 0%, #3a3a3a 45%, #c9d2e0 75%, #eef2f8 100%);
  }
  .cyclist-art {
    position: absolute; left: 805px; top: 38px; width: 330px; height: 405px;
    border-radius: 40% 45% 35% 40%;
    background: radial-gradient(ellipse at 50% 50%, #e2e2e2 0%, #efefef 55%, rgba(255,255,255,0) 75%);
  }

  .connectors { position: absolute; left: 0; top: 0; width: 1200px; height: 848px; pointer-events: none; }

  .award { position: absolute; left: 496px; display: flex; align-items: flex-start; }
  .award-number {
    width: 50px; height: 50px; border-radius: 50%; flex: none;
    color: var(--paper); font-style: italic; font-weight: 700; font-size: 38px;
    display: flex; align-items: center; justify-content: center; letter-spacing: -3px;
  }
  .award-number.green { background: var(--green); }
  .award-number.dark { background: var(--charcoal); }
  .award-text { margin-left: 8px; margin-top: 8px; font-weight: 700; font-size: 8.5px; line-height: 11px; }
  .award-text .win { color: var(--blue); font-size: 15px; line-height: 15px; }
  .award-text .of { font-size: 11px; }
  .award-text .small { font-size: 7px; }
  .award-1 { top: 226px; }
  .award-2 { top: 305px; }
  .award-3 { top: 395px; }

  .copy-panel {
    position: absolute; left: 35px; top: 526px; width: 637px; height: 295px;
    background: var(--green-panel); border-radius: 14px; padding: 20px 24px 16px;
    display: flex; flex-direction: column; color: var(--body-ink);
  }
  .strapline { font-size: 17px; line-height: 21px; font-weight: 700; color: var(--ink); }
  .strapline .accent { color: var(--green-deep); }
  .copy-columns { margin-top: 12px; column-count: 2; column-gap: 26px; font-size: 10.2px; line-height: 13.4px; }
  .copy-columns p { margin-bottom: 6px; break-inside: avoid; }
  .copy-columns .punch { font-weight: 700; color: var(--green-deep); }
  .panel-foot {
    margin-top: auto; padding-top: 9px; border-top: 1px solid rgba(79,138,52,.45);
    display: flex; justify-content: space-between; align-items: center; font-size: 10.5px;
  }
  .contact { font-weight: 700; color: var(--ink); }
  .contact span + span { margin-left: 16px; }
  .maker { display: flex; align-items: center; gap: 7px; font-size: 9px; }
  .maker-name { font-size: 13px; font-weight: 700; color: var(--ink); }

  .brand-block { position: absolute; left: 712px; top: 542px; }
  .brand-name {
    width: 84px; height: 40px; background: var(--ink); color: var(--paper);
    font-weight: 700; font-size: 10px; letter-spacing: .5px; text-transform: uppercase;
    display: flex; align-items: flex-end; justify-content: center; padding-bottom: 7px;
  }
  .brand-tag { margin-top: 4px; font-size: 6.5px; font-weight: 700; }

  .photo-hero-helmet {
    left: 748px; top: 610px; width: 188px; height: 185px; border-radius: 45% 45% 20% 20%;
    background: radial-gradient(ellipse 70% 60% at 50% 50%, #2c2c2c 0%, #3b3b3b 60%, rgba(255,255,255,0) 72%);
  }
  .fold-step { background: radial-gradient(ellipse 60% 50% at 50% 50%, #2f2f2f 0%, #3d3d3d 60%, rgba(255,255,255,0) 75%); }
  .fold-1 { left: 1003px; top: 542px; width: 98px; height: 50px; }
  .fold-2 { left: 1012px; top: 605px; width: 74px; height: 58px; }
  .fold-3 { left: 1013px; top: 676px; width: 74px; height: 58px; }
  .fold-4 { left: 1018px; top: 740px; width: 62px; height: 94px; }
</style>
</head>
<body>
<main class="sheet">
  <div class="rail-vertical"></div>
  <div class="band-faint"></div>
  <div class="band-divider"></div>

  <h1 class="headline">A Corporate<br>With <span class="accent">Recognition.</span></h1>

  <div class="photo photo-award-helmet" role="img" aria-label="Rendered black Vantrel folding cycle helmet, three-quarter view"></div>
  <div class="cyclist-art" role="img" aria-label="Faint grey silhouette illustration of a cyclist riding a road bike"></div>

  <svg class="connectors" viewBox="0 0 1200 848" aria-hidden="true">
    <line x1="344" y1="252" x2="498" y2="252" stroke="#7dc35b" stroke-width="1.5"/>
    <circle cx="344" cy="252" r="5" fill="#7dc35b"/>
    <line x1="345" y1="329" x2="488" y2="329" stroke="#6b6b6b" stroke-width="1.5"/>
    <circle cx="488" cy="329" r="6" fill="#555555"/>
    <line x1="344" y1="420" x2="498" y2="420" stroke="#7dc35b" stroke-width="1.5"/>
    <circle cx="344" cy="420" r="5" fill="#7dc35b"/>
  </svg>

  <section class="awards">
    <div class="award award-1">
      <div class="award-number green">01</div>
      <p class="award-text"><span class="win">Winner</span> <span class="of">of</span><br>Platinum Invetion of the year<br><span class="small">At The Global Ingenuity Prizes.</span></p>
    </div>
    <div class="award award-2">
      <div class="award-number dark">02</div>
      <p class="award-text" style="margin-top:10px"><span class="win">Winner</span> <span class="of">of</span><br>“Transport Safety” Award<br>&nbsp;&nbsp;At Kestra.</p>
    </div>
    <div class="award award-3">
      <div class="award-number green">03</div>
      <p class="award-text"><span class="win">Winner</span> <span class="of">of</span><br>“Lumora Zenith Gold Award”<br>&nbsp;&nbsp;For Innovation.</p>
    </div>
  </section>

  <section class="copy-panel">
    <h2 class="strapline">Vantrel<sup class="tm">TM</sup>… <span class="accent">an open and shut case for the future of helmets.</span></h2>
    <div class="copy-columns">
      <p>Vantrel<sup class="tm">TM</sup> is an incredibly innovative new helmet which folds flat for easy portability! (Current helmets are awkward to carry and research shows this is why 91% of urban bike scheme users don’t use one.)</p>
      <p>Vantrel<sup class="tm">TM</sup> looks stunning &amp; is made to a superb standard by Quillon Gear, the world’s largest OEM helmet manufacturer. It’s made in specialist EPS, Nylon &amp; PC layers.</p>
      <p>Patented worldwide, Vantrel<sup class="tm">TM</sup> surpasses all relevant safety standards and its components are recyclable. It folds &amp; unfolds quickly and simply, so it’s perfect for cyclists who want to carry a helmet more easily.</p>
      <p class="punch">It’s comfortable, convenient &amp; safe!</p>
      <p>Vantrel<sup class="tm">TM</sup> is aimed at all cyclists. Eventually it will be marketed to other users of sports safety helmets such as skiers, skaters, snow boarders, hockey players, horse riders etc.</p>
      <p>Vantrel<sup class="tm">TM</sup> has won major innovation awards in the UK and Europe. Its flat profile will allow innovative selling methods such as vending machines placed by major bicycle hire points.</p>
    </div>
    <footer class="panel-foot">
      <p class="contact"><span>info@vantrelhelmet.example</span><span>www.vantrelhelmet.example</span></p>
      <p class="maker">Manufactured by <span class="maker-name">Quillon Gear</span></p>
    </footer>
  </section>

  <div class="brand-block">
    <div class="brand-name">Vantrel</div>
    <p class="brand-tag">folding helmet technology</p>
  </div>

  <div class="photo photo-hero-helmet" role="img" aria-label="Rendered black Vantrel folding helmet, unfolded"></div>
  <div class="photo fold-step fold-1" role="img" aria-label="Helmet beginning to fold"></div>
  <div class="photo fold-step fold-2" role="img" aria-label="Helmet partly folded"></div>
  <div class="photo fold-step fold-3" role="img" aria-label="Helmet nearly folded"></div>
  <div class="photo fold-step fold-4" role="img" aria-label="Helmet folded flat"></div>
</main>
</body>
</html>
```